VFX Company Business Card Design Project

The Kestrel Works is a decentralized Visual Effects Studio servicing the television and feature film industries.
Project Brief:
Take our logo that was previously designed on Pencil Harbor and make a double sided business card.
Requirements:
- Card MUST be double sided.
- Front of card MUST have the yellow part of our logo against the dark grey background.
- Back of card is completely up to the designer.
- Back of card must include the complete company logo.
Please follow these File Preparation guidelines:
http://printnook.ca/infopage?file=filetype_en&s=PrintNook_new&lang=en
Business

```html
<!DOCTYPE html>
<html lang="en">
<head>
<meta charset="utf-8">
<title>The Kestrel Works – Business Cards</title>
<link rel="stylesheet" href="https://fonts.googleapis.com/css2?family=Jost:wght@400;500;600&display=swap">
<style>
  :root {
    --backdrop: #8a4a22;
    --card-dark: #262626;
    --card-light: #e9eee4;
    --card-slate: #5e6b6d;
    --accent-yellow: #fbc52b;
    --ink-dark: #262626;
    --ink-grey: #8a9496;
    --ink-white: #ffffff;
  }
  * { box-sizing: border-box; margin: 0; padding: 0; }
  html, body { width: 1200px; height: 733px; overflow: hidden; }
  body {
    background: var(--backdrop);
    font-family: "Jost", "Futura", sans-serif;
    position: relative;
  }
  .card {
    position: absolute;
    width: 524px;
    height: 299px;
    border-radius: 28px;
    overflow: hidden;
  }
  .card--front { left: 70px; top: 44px; background: var(--card-dark); }
  .card--contact { left: 631px; top: 48px; background: var(--card-dark); border: 1px solid #bbb; }
  .card--light { left: 66px; top: 385px; background: var(--card-light); }
  .card--slate { left: 625px; top: 389px; background: var(--card-slate); }

  .brand {
    display: flex;
    align-items: center;
    gap: 14px;
    position: absolute;
    font-weight: 600;
    white-space: nowrap;
    letter-spacing: 0.5px;
  }
  .brand__dot { border-radius: 50%; flex: none; }

  .card--front .brand {
    left: 0; right: 0; top: 0; bottom: 0;
    justify-content: center;
    color: var(--accent-yellow);
    font-size: 44px;
  }
  .card--front .brand__dot { width: 34px; height: 34px; background: var(--accent-yellow); }

  .card--contact .brand {
    left: 24px; top: 124px;
    color: var(--ink-grey);
    font-size: 25px;
  }

  .contact-strip {
    position: absolute;
    left: 298px; top: 44px;
    width: 21px; height: 210px;
    background: var(--card-slate);
  }
  .contact-strip__url {
    position: absolute;
    left: 50%; top: 50%;
    transform: translate(-50%, -50%) rotate(-90deg);
    color: var(--ink-white);
    font-size: 11.5px;
    letter-spacing: 1px;
    white-space: nowrap;
  }
  .contact-panel {
    position: absolute;
    left: 322px; top: 44px;
    width: 202px; height: 210px;
    background: var(--card-light);
    padding: 20px 0 0 16px;
    color: var(--ink-dark);
  }
  .contact-panel__name { font-size: 20px; font-weight: 600; line-height: 1.1; }
  .contact-panel__title { font-size: 14px; margin: 4px 0 12px; }
  .contact-list { list-style: none; font-size: 13px; line-height: 20px; }
  .contact-list li { display: flex; align-items: flex-start; gap: 6px; }
  .contact-list svg { width: 11px; height: 11px; margin-top: 5px; flex: none; fill: var(--ink-dark); }
  .contact-list .contact-list__address { margin-top: 8px; line-height: 17px; }

  .card--light .brand {
    left: 0; right: 0; top: 104px;
    justify-content: center;
    color: var(--ink-dark);
    font-size: 40px;
  }
  .card--light .brand__dot { width: 30px; height: 30px; background: var(--ink-dark); }

  .card--slate .brand {
    left: 0; right: 0; top: 100px;
    justify-content: center;
    color: var(--ink-white);
    font-size: 46px;
  }

  .card__url {
    position: absolute;
    left: 0; right: 0; bottom: 22px;
    text-align: center;
    font-size: 17px;
    letter-spacing: 2.5px;
  }
  .card--light .card__url { color: var(--ink-dark); }
  .card--slate .card__url { color: var(--ink-white); }
</style>
</head>
<body>

  <section class="card card--front" aria-label="Card front">
    <div class="brand"><span class="brand__dot"></span>The Kestrel Works</div>
  </section>

  <section class="card card--contact" aria-label="Card back with contact details">
    <div class="brand">The Kestrel Works</div>
    <div class="contact-strip"><span class="contact-strip__url">www.kestrelworks.com</span></div>
    <div class="contact-panel">
      <p class="contact-panel__name">Your Name</p>
      <p class="contact-panel__title">Title</p>
      <ul class="contact-list">
        <li><svg viewBox="0 0 12 12"><path d="M3 1l2 2.5-1.2 1.3a7 7 0 0 0 3.4 3.4L8.5 7 11 9l-1.2 2C5.5 11 1 6.5 1 2.2z"/></svg>0987 654321</li>
        <li><svg viewBox="0 0 12 12"><rect x="3" y="0.5" width="6" height="11" rx="1.2"/></svg>0987 654321</li>
        <li><svg viewBox="0 0 12 12"><path d="M0.5 2.5h11v7h-11z M1 3l5 3.5L11 3" stroke="#e9eee4" stroke-width="0.8"/></svg>info@kestrelworks.com</li>
        <li class="contact-list__address"><svg viewBox="0 0 12 12"><circle cx="6" cy="6" r="5.5"/><circle cx="6" cy="5" r="1.6" fill="#e9eee4"/></svg><span>00, Complex name<br>City, State 0042</span></li>
      </ul>
    </div>
  </section>

  <section class="card card--light" aria-label="Card back, light version">
    <div class="brand"><span class="brand__dot"></span>The Kestrel Works</div>
    <p class="card__url">www.kestrelworks.com</p>
  </section>

  <section class="card card--slate" aria-label="Card back, slate version">
    <div class="brand">The Kestrel Works</div>
    <p class="card__url">www.kestrelworks.com</p>
  </section>

</body>
</html>
```